Modern design company business card design

We are a design oriented construction firm. The owner is an architect and licensed General Contractor and accomplished furniture designer. We do new home construction and large scale remodeling and office design. We would like a design for our new business cards that is clean and modern, but relatable. We like the bright green color of our logo mixed with different shades of grey. We're also open to reinterpreting the logo.

Target Market(s)

Potential design clients,
Construction clients

Industry/Entity Type

Architecture

Contact Information for Business Card

Tall Maple Design | Build Inc. (optional with logo, Inc. optional)Jeffrey MorganOwner (optional)317.555.0148 cell317.431.8056 officejmorgan@greensquareinc.comwww.greensquareinc.com

Font styles to use
Sans Serif
Other font styles liked:
• Avenir

Requirements
Nice to have
• I like designs that have some continuity between the front and back, i.e. similar layouts or graphic elements that wrap around the card. I tend to prefer horizontal over vertical, but that's not a have to. I also tend to prefer white or recycled paper.

```html
<!DOCTYPE html>
<html lang="en">
<head>
<meta charset="utf-8">
<title>Tall Maple Design | Build — Business Card</title>
<link rel="stylesheet" href="https://fonts.googleapis.com/css2?family=Mulish:wght@400;600&display=swap">
<style>
  :root {
    --page-bg: #d9dbd8;
    --card-bg: #eef0ee;
    --card-edge: #ffffff;
    --green-light: #8fca44;
    --green-dark: #5c9f1e;
    --icon-green: #66a82a;
    --text-grey: #4b4d4c;
    --text-soft: #5e605f;
    --white: #ffffff;
  }
  * { margin: 0; padding: 0; box-sizing: border-box; }
  html, body {
    width: 1200px; height: 969px; overflow: hidden;
    background: var(--page-bg);
    font-family: "Mulish", "Nunito Sans", sans-serif;
  }
  .canvas { position: relative; width: 1200px; height: 969px; }
  .business-card {
    position: absolute; left: 75px; top: 186px;
    width: 1050px; height: 596px;
    background: var(--card-bg);
    border: 1px solid var(--card-edge);
    box-shadow: 0 10px 30px rgba(0,0,0,0.12);
    overflow: hidden;
  }
  .name-band {
    position: absolute; left: 0; top: 74px;
    width: 486px; height: 157px;
    background: linear-gradient(180deg, var(--green-light), var(--green-dark));
  }
  .holder-name {
    position: absolute; left: 60px; top: 116px;
    font-size: 36px; font-weight: 600; color: var(--white);
    letter-spacing: 0.2px;
  }
  .holder-title {
    position: absolute; left: 60px; top: 164px;
    font-size: 26px; font-weight: 400; color: var(--white);
  }
  .brand-name {
    position: absolute; right: 62px; top: 168px;
    text-align: right; color: var(--text-soft);
    font-weight: 400;
  }
  .brand-name .brand-main {
    display: block; font-size: 46px; letter-spacing: 3px; line-height: 1;
  }
  .brand-name .brand-sub {
    display: block; font-size: 19px; letter-spacing: 2.5px; margin-top: 14px;
  }
  .contact-list {
    position: absolute; left: 60px; top: 378px;
    list-style: none;
  }
  .contact-list li {
    display: flex; align-items: center;
    height: 41px;
    font-size: 28px; color: var(--text-grey);
  }
  .contact-list svg {
    width: 26px; height: 26px; margin-right: 16px; flex: none;
    fill: var(--icon-green);
  }
</style>
</head>
<body>
<div class="canvas">
  <div class="business-card">
    <div class="name-band"></div>
    <div class="holder-name">Dennis Holloway</div>
    <div class="holder-title">Owner</div>

    <div class="brand-name">
      <span class="brand-main">TALL MAPLE</span>
      <span class="brand-sub">DESIGN | BUILD</span>
    </div>

    <ul class="contact-list">
      <li>
        <svg viewBox="0 0 24 24" aria-hidden="true"><path d="M6.6 10.8a15.1 15.1 0 0 0 6.6 6.6l2.2-2.2c.3-.3.7-.4 1-.2 1.1.4 2.300.6 3.6.6.6 0 1 .4 1 1V20c0 .6-.4 1-1 1A17 17 0 0 1 3 4c0-.6.4-1 1-1h3.5c.6 0 1 .4 1 1 0 1.3.2 2.5.6 3.6.1.3 0 .7-.2 1z"/></svg>
        317.555.0148
      </li>
      <li>
        <svg viewBox="0 0 24 24" aria-hidden="true"><path d="M7 1h10a2 2 0 0 1 2 2v18a2 2 0 0 1-2 2H7a2 2 0 0 1-2-2V3a2 2 0 0 1 2-2zm0 3v14h10V4zm5 15.5a1.2 1.2 0 1 0 0 2.4 1.2 1.2 0 0 0 0-2.4z"/></svg>
        317.555.0172
      </li>
      <li>
        <svg viewBox="0 0 24 24" aria-hidden="true"><path d="M12 2a10 10 0 1 0 0 20 10 10 0 0 0 0-20zm6.9 6h-2.9a15.6 15.6 0 0 0-1.4-3.6A8 8 0 0 1 18.9 8zM12 4c.8 1.2 1.5 2.5 1.9 4h-3.8c.4-1.5 1.1-2.8 1.9-4zM4.3 14a8 8 0 0 1 0-4h3.4a16 16 0 0 0 0 4zm.8 2h2.9c.3 1.3.8 2.5 1.4 3.6A8 8 0 0 1 5.1 16zM8 8H5.1a8 8 0 0 1 4.3-3.6C8.8 5.5 8.3 6.7 8 8zm4 12c-.8-1.2-1.5-2.5-1.9-4h3.8c-.4 1.5-1.1 2.8-1.9 4zm2.3-6H9.7a14.7 14.7 0 0 1 0-4h4.6a14.7 14.7 0 0 1 0 4zm.3 5.6c.6-1.1 1.1-2.3 1.4-3.6h2.9a8 8 0 0 1-4.3 3.6zm1.7-5.6a16 16 0 0 0 0-4h3.4a8 8 0 0 1 0 4z"/></svg>
        www.tallmapleinc.example
      </li>
      <li>
        <svg viewBox="0 0 24 24" aria-hidden="true"><path d="M3 5h18a1 1 0 0 1 1 1v12a1 1 0 0 1-1 1H3a1 1 0 0 1-1-1V6a1 1 0 0 1 1-1zm1 2.3V17h16V7.3l-8 5.2z M4.5 7h15L12 11.9z"/></svg>
        dholloway@tallmapleinc.example
      </li>
    </ul>
  </div>
</div>
</body>
</html>
```